Build PowerPoint for New Logo & Letterhead

I have started my own consulting firm and created a logo and letterhead (attached) am looking PowerPoint template. My name is Dorrit Vandermolen and the company is called K Quadrant Advisory. We primarily use PowerPoint files to display analyses, maps and key talking points from interviews and/or recommendations. We use the documents more to facilitate discussion with our target audiences. Most of the time our PowerPoint document is printed as handouts for our clients and not projected.

Target Market(s)

Healthcare provider organizations (hospitals, health systems, physician groups)

Industry/Entity Type

Healthcare

Font styles to use
Sans Serif

Colors
abd036
1f9ad1
0355a3

Requirements
Must have
• I would like to cover page to play off of the letterhead in some fashion. I want the design to provide plenty of space for text, graphics, maps, pictures, etc.
• We will usually include our clients logo somewhere on the document. Historically it is prominent on the cover page and then in one of the corners on all of the pages thereafter.

```html
<!DOCTYPE html>
<html lang="en">
<head>
<meta charset="utf-8">
<title>Annual Graphs</title>
<link rel="stylesheet" href="https://fonts.googleapis.com/css2?family=Roboto+Condensed:wght@400;700&display=swap">
<style>
  :root {
    --green: #9ccc3c;
    --blue-deep: #0a5fae;
    --blue-bright: #1f9ad1;
    --heading-blue: #1565b8;
    --text: #3d3d3d;
    --axis: #c9c9c9;
    --page: #f7f7f7;
    --white: #ffffff;
  }
  * { margin: 0; padding: 0; box-sizing: border-box; }
  html, body { width: 1200px; height: 900px; overflow: hidden; }
  body {
    background: var(--page);
    font-family: "Roboto Condensed", "Arial Narrow", sans-serif;
    color: var(--text);
  }
  .slide { position: relative; width: 1200px; height: 900px; overflow: hidden; background: var(--page); }
  .header-band, .footer-band { position: absolute; left: 0; }
  .header-band { top: 0; }
  .footer-band { bottom: 0; }
  .slide-title {
    position: absolute; left: 22px; top: 12px;
    font-size: 44px; font-weight: 700; color: var(--white);
    letter-spacing: 0.5px;
  }
  .brand-name {
    position: absolute; right: 18px; top: 24px;
    font-size: 19px; font-weight: 700; color: var(--heading-blue);
  }
  .section-heading {
    position: absolute; left: 36px; top: 142px;
    font-size: 32px; font-weight: 700; color: var(--heading-blue);
    padding-bottom: 4px;
    border-bottom: 2px solid var(--blue-bright);
  }
  .text-column { position: absolute; left: 31px; top: 240px; width: 500px; }
  .subtitle { font-size: 29px; font-weight: 700; color: var(--green); line-height: 40px; }
  .body-copy { font-size: 22px; line-height: 39px; }
  .body-copy + .body-copy { margin-top: 39px; }
  .chart { position: absolute; left: 0; top: 0; }
  .chart text { font-family: "Roboto Condensed", "Arial Narrow", sans-serif; fill: var(--text); }
  .copyright {
    position: absolute; left: 12px; bottom: 16px;
    font-size: 21px; color: var(--white);
  }
</style>
</head>
<body>
<main class="slide">
  <svg class="header-band" width="1200" height="80" viewBox="0 0 1200 80" aria-hidden="true">
    <defs>
      <linearGradient id="headerFill" x1="0" x2="1" y1="0" y2="0">
        <stop offset="0" stop-color="#0a5fae"/>
        <stop offset="1" stop-color="#15a6ea"/>
      </linearGradient>
    </defs>
    <rect width="1200" height="80" fill="#ffffff"/>
    <polygon points="0,0 1058,0 1003,78 0,78" fill="url(#headerFill)"/>
  </svg>
  <h1 class="slide-title">PROJECT TITLE HERE</h1>
  <div class="brand-name">K Quadrant Advisory</div>

  <h2 class="section-heading">ANNUAL GRAPHS</h2>

  <section class="text-column">
    <h3 class="subtitle">Subtext Title here</h3>
    <p class="body-copy">Lorem Ipsum is simply dummy text of the printing and typesetting industry. Lorem Ipsum has been the industry's standard dummy text ever since the 1500s, when an unknown printer took a galley of type and scrambled it to make a type specimen book. Lorem Ipsum is simply dummy text of the printing and typesetting industry.</p>
    <p class="body-copy">Lorem Ipsum has been the industry's standard dummy text ever since the 1500s, when an unknown printer took a galley of type and scrambled it to make a type specimen book.</p>
  </section>

  <svg class="chart" width="1200" height="900" viewBox="0 0 1200 900" role="img" aria-label="Stacked bar chart of monthly totals by solution">
    <g class="grid" stroke="var(--axis)" stroke-width="1.5">
      <line x1="637" y1="258" x2="1200" y2="258"/>
      <line x1="637" y1="350" x2="1200" y2="350"/>
      <line x1="637" y1="443" x2="1200" y2="443"/>
      <line x1="637" y1="535" x2="1200" y2="535"/>
      <line x1="637" y1="627" x2="1200" y2="627"/>
      <line x1="637" y1="248" x2="637" y2="642"/>
    </g>
    <g class="y-labels" font-size="22" text-anchor="end">
      <text x="617" y="266">2000</text>
      <text x="617" y="358">1500</text>
      <text x="617" y="451">1000</text>
      <text x="617" y="543">500</text>
      <text x="617" y="635">0</text>
    </g>
    <g class="bars">
      <rect x="663" y="366" width="137" height="261" fill="var(--green)"/>
      <rect x="663" y="277" width="137" height="89" fill="var(--blue-deep)"/>
      <rect x="836" y="366" width="136" height="261" fill="var(--green)"/>
      <rect x="836" y="304" width="136" height="62" fill="var(--blue-deep)"/>
      <rect x="1008" y="366" width="137" height="261" fill="var(--green)"/>
      <rect x="1008" y="336" width="137" height="30" fill="var(--blue-deep)"/>
    </g>
    <g class="x-labels" font-size="22" text-anchor="middle">
      <text x="731" y="664">DEC-15</text>
      <text x="904" y="664">JAN-15</text>
      <text x="1076" y="664">fevr-2016</text>
    </g>
    <g class="legend" font-size="22">
      <rect x="664" y="720" width="26" height="26" fill="var(--blue-deep)"/>
      <text x="702" y="741">Solution IT Internet Mobile</text>
      <rect x="664" y="779" width="26" height="26" fill="var(--green)"/>
      <text x="702" y="800">Solution Telephone</text>
    </g>
  </svg>

  <svg class="footer-band" width="1200" height="58" viewBox="0 0 1200 58" aria-hidden="true">
    <rect x="0" y="30" width="1200" height="28" fill="var(--green)"/>
    <polygon points="0,0 247,0 272,30 272,58 0,58" fill="var(--green)"/>
  </svg>
  <p class="copyright">Copyright text here</p>
</main>
</body>
</html>
```